Laser Tattoo Removal Business Cards

We are looking for a professional business card design for a laser tattoo removal business. Ideally looking for a black business card design. The name of the business is Brightline Tattoo Removal. We place our cards at local tattoo shops so we ideally are looking for something trendy/edgy to draw both male and female clientele in.

Target Market(s)

Male/Female ages 18-60

Contact Information for Business Card

black background ideally.. hoping to stay within greys, whites and black

Font styles to use
Serif
Sans Serif

Colors
121212
a9a9a9
5c5c5c
f5f5f5
ffffff
7f7f7f
606060
848484
9d9d9d

Requirements
Must have
• Employee Info:
• Melissa Thornbury
• Chief Executive Offer
• m: 919.537.2846
• w: 919.362.4178
• f: 919.685.3907
• mthornbury@brightlinetattooremoval.example
• Address:
• 4615 Oakmere Pkwy, Suite 210
• Raleigh, NC 27654
• Website:
• www.brightlinetattooremoval.example
Nice to have
• Myabe business name on back or logo on back and employee info on the front

```html
<!DOCTYPE html>
<html lang="en">
<head>
<meta charset="utf-8">
<title>Brightline Tattoo Removal – Business Cards</title>
<link rel="stylesheet" href="https://fonts.googleapis.com/css2?family=Oswald:wght@500&family=Jost:wght@400&family=Roboto:wght@400&display=swap">
<style>
  :root {
    --backdrop: #5a4a3b;
    --card-light: #f5f5f5;
    --card-dark: #121212;
    --ink: #121212;
    --ink-soft: #5c5c5c;
    --ink-muted: #9d9d9d;
    --paper-white: #ffffff;
  }
  * { margin: 0; padding: 0; box-sizing: border-box; }
  html, body { width: 1200px; height: 960px; overflow: hidden; }
  body { background: var(--backdrop); position: relative; }

  .card {
    position: absolute;
    width: 600px;
    height: 342px;
    box-shadow: 2px 3px 6px rgba(0,0,0,0.35);
  }
  .card--front { left: 322px; top: 108px; background: var(--card-light); }
  .card--back  { left: 320px; top: 493px; background: var(--card-dark); }

  .brand {
    position: absolute;
    font-family: "Oswald", sans-serif;
    font-weight: 500;
    text-align: center;
    text-transform: uppercase;
    line-height: 1.15;
  }
  .brand__name { display: block; letter-spacing: 0.08em; }
  .brand__line { display: block; letter-spacing: 0.12em; }

  .card--front .brand { left: 360px; top: 42px; width: 216px; color: var(--ink-soft); }
  .card--front .brand__name { font-size: 40px; }
  .card--front .brand__line { font-size: 18px; margin-top: 14px; }

  .card--back .brand { left: 150px; top: 100px; width: 300px; color: var(--paper-white); }
  .card--back .brand__name { font-size: 50px; }
  .card--back .brand__line { font-size: 20px; margin-top: 18px; }

  .tab {
    position: absolute;
    left: 0; top: 175px;
    width: 8px; height: 40px;
    background: var(--ink);
  }
  .contact { position: absolute; left: 27px; top: 175px; font-family: "Jost", sans-serif; }
  .contact__name {
    font-family: "Oswald", sans-serif;
    font-weight: 500;
    font-size: 21px;
    line-height: 24px;
    color: var(--ink);
    text-transform: uppercase;
  }
  .contact__title { font-size: 15px; color: var(--ink-muted); line-height: 20px; margin-bottom: 6px; }
  .contact__line { font-size: 14px; color: var(--ink-soft); line-height: 19.5px; }
  .contact__line--address { font-size: 15px; margin-top: 2px; }

  .web {
    position: absolute;
    left: 0; right: 0; top: 292px;
    text-align: center;
    font-family: "Roboto", sans-serif;
    font-size: 15px;
    letter-spacing: 0.16em;
    color: var(--paper-white);
  }
</style>
</head>
<body>
  <section class="card card--front">
    <div class="brand">
      <span class="brand__name">Brightline</span>
      <span class="brand__line">Tattoo Removal</span>
    </div>
    <div class="tab"></div>
    <div class="contact">
      <p class="contact__name">Melissa Thornbury</p>
      <p class="contact__title">Chief Executive Offer</p>
      <p class="contact__line">P.919.362.4178</p>
      <p class="contact__line">M.919.537.2846 F.919.685.3907</p>
      <p class="contact__line">mthornbury@brightlinetattooremoval.example</p>
      <p class="contact__line">www.brightlinetattooremoval.example</p>
      <p class="contact__line contact__line--address">4615 Oakmere Pkwy, Suite 210, Raleigh, NC 27654</p>
    </div>
  </section>

  <section class="card card--back">
    <div class="brand">
      <span class="brand__name">Brightline</span>
      <span class="brand__line">Tattoo Removal</span>
    </div>
    <p class="web">www.brightlinetattooremoval.example</p>
  </section>
</body>
</html>
```